Forensic Document Examiner, looking for contemporary update to my stationery design.

Looking for professional, classy logo design for stationery and business cards. My current stationery and business card is attached.I believe a logo image makes a header section interesting, so an intriguing design of a pen, feathered pen, microscope, magnifying glass, etc., would be appropriate. I have been in the business for over 30 years. I leave ideas to the imagination of the designer.My work involves mainly, the comparison of signatures and handwriting. I also resolve alterations, obliterations, and work as shown on my website: www.documentexaminer.infoThe image produced will be printed on quality white stationery and envelopes. The stationery will be photocopied by my clients, so the images should be reproducible. The business cards may be designed in other than white.

Target Market(s)

Attorneys

Font styles to use
Sans Serif

Colors

Designer to choose colors to be used in the design.

Requirements
Must have
• Image suitable for white stationery and photocopying.
• Classy logo and image; no casual fonts.
Nice to have
• Intriguing, contemporary design incorporating a relevant logo to my work.

```html
<!DOCTYPE html>
<html lang="en">
<head>
<meta charset="utf-8">
<title>Daniel R. Whitford – Business Card</title>
<link href="https://fonts.googleapis.com/css2?family=Source+Sans+3:ital,wght@0,400;0,600;1,400&display=swap" rel="stylesheet">
<style>
  :root {
    --page: #e9e7e4;
    --card-dark: #2f2f2f;
    --card-darker: #212121;
    --panel-blue: #2f2e8f;
    --panel-navy: #1d1b5c;
    --accent-gold: #f0cd2a;
    --text-light: #d6d6e4;
    --text-white: #f2f2f2;
    --tagline: #c9c9c9;
    --mark-fill: #3a3a3a;
  }
  * { margin: 0; padding: 0; box-sizing: border-box; }
  html, body {
    width: 1125px; height: 1200px; overflow: hidden;
    background: var(--page);
    font-family: "Source Sans 3", sans-serif;
  }
  .canvas { position: relative; width: 1125px; height: 1200px; }

  .card {
    position: absolute; left: 150px; width: 825px; height: 471px;
    border-radius: 24px; overflow: hidden;
    box-shadow: 0 4px 10px rgba(0,0,0,0.25);
  }
  .card-front { top: 98px; display: flex; }
  .card-back {
    top: 632px;
    background: linear-gradient(90deg, var(--card-darker) 0%, var(--card-dark) 45%, var(--card-dark) 100%);
  }

  .front-brand {
    width: 406px; height: 100%; background: var(--card-dark);
    display: flex; align-items: center; justify-content: center; gap: 14px;
  }
  .brand-dot { width: 18px; height: 18px; border-radius: 50%; background: var(--accent-gold); }
  .brand-name { color: var(--text-white); font-size: 34px; font-weight: 600; letter-spacing: 1px; }

  .front-divider { width: 3px; height: 100%; background: var(--accent-gold); }

  .front-contact {
    flex: 1; height: 100%; padding: 127px 0 0 44px;
    background: linear-gradient(90deg, var(--panel-blue) 0%, var(--panel-blue) 30%, var(--panel-navy) 100%);
    color: var(--text-light);
  }
  .contact-name { color: var(--accent-gold); font-size: 29px; font-weight: 600; line-height: 1.1; }
  .contact-role { font-size: 20px; line-height: 1.2; margin-bottom: 18px; }
  .contact-address { font-size: 18px; line-height: 1.4; margin-bottom: 13px; }
  .contact-list { list-style: none; font-size: 18px; line-height: 1.4; }
  .contact-list li { display: flex; align-items: center; gap: 8px; }
  .contact-list svg { width: 17px; height: 17px; flex: none; }

  .back-mark {
    position: absolute; left: 292px; top: 90px; width: 190px; height: 190px;
    display: flex; align-items: center; justify-content: center;
  }
  .back-mark-circle { width: 190px; height: 190px; border-radius: 50%; background: var(--mark-fill); }
  .back-name {
    position: absolute; left: 0; right: 0; top: 300px; text-align: center;
    color: var(--text-white); font-size: 26px; font-weight: 600; letter-spacing: 1px;
  }
  .back-tagline {
    position: absolute; left: 0; right: 0; top: 360px; text-align: center;
    color: var(--tagline); font-style: italic; font-size: 18px; line-height: 1.35;
  }
</style>
</head>
<body>
<main class="canvas">
  <section class="card card-front">
    <div class="front-brand">
      <span class="brand-dot"></span>
      <span class="brand-name">DANIEL R. WHITFORD</span>
    </div>
    <div class="front-divider"></div>
    <div class="front-contact">
      <h1 class="contact-name">Daniel R. Whitford</h1>
      <p class="contact-role">Forensic document Examiner</p>
      <p class="contact-address">P.O.Box 2184<br>Salem, OR 97301</p>
      <ul class="contact-list">
        <li>
          <svg viewBox="0 0 24 24" aria-hidden="true"><path fill="#f0cd2a" d="M6.6 10.8a15 15 0 0 0 6.6 6.6l2.2-2.2c.3-.3.7-.4 1-.2 1.1.4 2.3.6 3.6.6.6 0 1 .4 1 1V20c0 .6-.4 1-1 1A17 17 0 0 1 3 4c0-.6.4-1 1-1h3.5c.6 0 1 .4 1 1 0 1.3.2 2.5.6 3.6.1.3 0 .7-.2 1z"/></svg>
          (888) 555-0174
        </li>
        <li>
          <svg viewBox="0 0 24 24" aria-hidden="true"><rect x="2" y="5" width="20" height="14" rx="1" fill="#f0cd2a"/><path d="M2 6l10 7 10-7" fill="none" stroke="#2f2e8f" stroke-width="1.6"/></svg>
          dwhitford@quillmarkreview.info
        </li>
        <li>
          <svg viewBox="0 0 24 24" aria-hidden="true"><circle cx="12" cy="12" r="10" fill="#f0cd2a"/><path d="M7 8c2 0 3 1 3 3s-2 2-2 4m7-9c-1 2 1 3 2 3m-3 6c1-1 3-1 3-3" fill="none" stroke="#2f2e8f" stroke-width="1.6"/></svg>
          www.quillmarkreview.info
        </li>
      </ul>
    </div>
  </section>

  <section class="card card-back">
    <div class="back-mark"><div class="back-mark-circle"></div></div>
    <p class="back-name">DANIEL R. WHITFORD</p>
    <p class="back-tagline">Full service laboratory, Specializing in handwriting comparisons,<br>obliterations, alterations, indented wrinting recovery, etc.</p>
  </section>
</main>
</body>
</html>
```